Brisk Plate all natural shake full body sleeve design label

We need a label design for a new product launch of Brisk Plate whole body nutrition shake. Full body sleeve shrink. We have uploaded a brief in pdf format to review with most details. Thank you in advance for your consideration.

The Tarven Hollow logo is our company logo, which will be small somewhere on the back / side of bottle where company info will be. Just thought it might spark something creative.

Industry/Entity Type

Nutrition

```html
<!DOCTYPE html>
<html lang="en">
<head>
<meta charset="utf-8">
<title>Brisk Plate Whole Body Nutritional Shake – Label</title>
<link rel="stylesheet" href="https://fonts.googleapis.com/css2?family=Oswald:wght@400;500;600&display=swap">
<style>
  :root {
    --paper: #ffffff;
    --brown-deep: #3d1a0c;
    --brown: #4a2414;
    --brown-mid: #6b3a2a;
    --brown-soft: #8f6a5c;
    --green: #7aa63a;
    --green-light: #9cc84a;
    --purple: #7b2a8c;
    --violet: #8a2a96;
    --magenta: #b5197d;
    --berry: #a0207e;
    --orange: #f0821e;
    --yellow: #f7c52c;
  }
  html, body {
    margin: 0;
    padding: 0;
    width: 927px;
    height: 1200px;
    overflow: hidden;
    background: var(--paper);
  }
  .label {
    display: block;
    width: 927px;
    height: 1200px;
    font-family: "Oswald", "Arial Narrow", sans-serif;
  }
  .label text { font-family: "Oswald", "Arial Narrow", sans-serif; }
  .product-line { font-weight: 600; font-size: 19px; fill: var(--brown); }
  .flavour { fill: var(--brown-mid); }
  .side-claim { font-weight: 500; font-size: 46px; fill: var(--brown); }
  .headline { font-weight: 500; }
  .benefit-immune { font-weight: 500; font-size: 56px; fill: var(--berry); }
  .benefit-digest { font-weight: 500; font-size: 56px; fill: var(--violet); }
  .liver { font-weight: 400; font-size: 150px; fill: var(--brown-deep); }
  .aches { font-weight: 400; font-size: 64px; fill: var(--brown-mid); }
  .natural { font-weight: 400; font-size: 56px; fill: var(--brown-soft); }
  .free-from { font-weight: 400; font-size: 148px; fill: var(--green); }
  .stat-figure { font-weight: 600; font-size: 30px; fill: var(--brown); }
  .stat-unit { font-weight: 400; font-size: 12px; fill: var(--brown-mid); }
  .icon { fill: var(--paper); }
  .icon-line { fill: none; stroke: var(--paper); stroke-width: 4; stroke-linecap: round; stroke-linejoin: round; }
</style>
</head>
<body>
<svg class="label" viewBox="0 0 927 1200" xmlns="http://www.w3.org/2000/svg" aria-label="Brisk Plate whole body nutritional shake label">
  <defs>
    <linearGradient id="grad-benefits" x1="0" y1="0" x2="0" y2="1">
      <stop offset="0" stop-color="#5f9a2e"/>
      <stop offset="1" stop-color="var(--green-light)"/>
    </linearGradient>
    <linearGradient id="grad-probiotics" x1="0" y1="0" x2="0" y2="1">
      <stop offset="0" stop-color="var(--orange)"/>
      <stop offset="1" stop-color="var(--yellow)"/>
    </linearGradient>
    <linearGradient id="grad-leaves" x1="0" y1="0" x2="1" y2="0">
      <stop offset="0" stop-color="#8fc23a"/>
      <stop offset="0.5" stop-color="#8fc23a"/>
      <stop offset="0.5" stop-color="#7a2a98"/>
      <stop offset="1" stop-color="#7a2a98"/>
    </linearGradient>
  </defs>

  <!-- product line -->
  <text class="product-line" x="463" y="40" text-anchor="middle">WHOLE BODY NUTRITIONAL SHAKE</text>
  <text class="product-line flavour" x="463" y="65" text-anchor="middle">CREAMY DARK CHOCOLATE GELATO</text>

  <!-- leaf illustration area -->
  <rect role="img" aria-label="Illustration of a green leaf and a purple leaf side by side"
        x="313" y="92" width="310" height="88" rx="44" fill="url(#grad-leaves)" opacity="0.85"/>

  <!-- left vertical claims -->
  <text class="side-claim" transform="translate(136 695) rotate(-90)" textLength="485" lengthAdjust="spacingAndGlyphs">16 GRAMS OF NON-GMO PEA PROTEIN</text>
  <text class="side-claim" transform="translate(201 695) rotate(-90)" textLength="485" lengthAdjust="spacingAndGlyphs">2 GRAMS DIETARY FIBER</text>

  <!-- central benefits stack -->
  <text class="headline" x="213" y="345" font-size="172" fill="url(#grad-benefits)" textLength="505" lengthAdjust="spacingAndGlyphs">BENEFITS</text>
  <text class="headline" x="213" y="410" font-size="64" fill="var(--purple)" textLength="505" lengthAdjust="spacingAndGlyphs">FRUITS &amp; VEGETABLES</text>
  <text class="headline" x="213" y="482" font-size="64" fill="var(--magenta)" textLength="505" lengthAdjust="spacingAndGlyphs">VITAMINS &amp; MINERALS</text>
  <text class="headline" x="213" y="578" font-size="100" fill="var(--orange)" textLength="505" lengthAdjust="spacingAndGlyphs">ANTIOXIDANTS</text>
  <text class="headline" x="213" y="695" font-size="135" fill="url(#grad-probiotics)" textLength="505" lengthAdjust="spacingAndGlyphs">PROBIOTICS</text>

  <!-- right vertical claims -->
  <text class="benefit-immune" transform="translate(735 210) rotate(90)" textLength="482" lengthAdjust="spacingAndGlyphs">IMMUNE SUPPORT</text>
  <text class="benefit-digest" transform="translate(795 210) rotate(90)" textLength="482" lengthAdjust="spacingAndGlyphs">DIGESTIVE ENZYMES</text>

  <!-- support claims -->
  <text class="liver" x="98" y="830" textLength="735" lengthAdjust="spacingAndGlyphs">LIVER SUPPORT</text>
  <text class="aches" x="98" y="905" textLength="735" lengthAdjust="spacingAndGlyphs">ACHES-PAIN-STIFFNESS SUPPORT</text>
  <text class="natural" x="98" y="970" textLength="735" lengthAdjust="spacingAndGlyphs">ALL NATURAL PLANT BASED VEGETARIAN</text>

  <!-- free-from band -->
  <rect x="213" y="988" width="620" height="112" fill="var(--green)"/>
  <path d="M207 988 Q232 1044 207 1100" fill="none" stroke="var(--paper)" stroke-width="8"/>
  <text class="free-from" x="96" y="1100" textLength="110" lengthAdjust="spacingAndGlyphs">NO</text>

  <g aria-label="Free from: dairy, sugar, gluten, soy, artificial additives, nuts, oil">
    <!-- dairy bottle -->
    <path class="icon" d="M266 1012 h14 v10 q10 8 10 20 v38 h-34 v-38 q0 -12 10 -20 z"/>
    <!-- sugar cube -->
    <path class="icon" d="M356 1022 l26 12 v28 l-26 12 l-26 -12 v-28 z"/>
    <path d="M330 1034 l26 12 l26 -12 M356 1046 v28" fill="none" stroke="var(--green)" stroke-width="3"/>
    <!-- wheat -->
    <path class="icon-line" d="M431 1016 v66"/>
    <path class="icon" d="M431 1020 q-12 6 -10 18 q10 -2 10 -14 z M431 1020 q12 6 10 18 q-10 -2 -10 -14 z M431 1040 q-12 6 -10 18 q10 -2 10 -14 z M431 1040 q12 6 10 18 q-10 -2 -10 -14 z M431 1058 q-12 6 -10 18 q10 -2 10 -14 z M431 1058 q12 6 10 18 q-10 -2 -10 -14 z"/>
    <!-- soy pod -->
    <path class="icon" d="M492 1020 q10 -8 18 2 q6 10 14 18 q12 10 10 24 q-4 12 -18 6 q-12 -8 -16 -22 q-4 -12 -8 -28 z"/>
    <!-- flask -->
    <path class="icon-line" d="M592 1016 h16 M595 1016 v22 l-18 36 h46 l-18 -36 v-22"/>
    <path class="icon" d="M583 1062 h34 l6 12 h-46 z"/>
    <!-- nuts -->
    <circle class="icon" cx="680" cy="1034" r="12"/>
    <circle class="icon" cx="702" cy="1034" r="12"/>
    <circle class="icon" cx="676" cy="1058" r="12"/>
    <circle class="icon" cx="700" cy="1058" r="12"/>
    <!-- drop -->
    <path class="icon" d="M768 1016 q-18 28 -18 42 a18 18 0 0 0 36 0 q0 -14 -18 -42 z"/>
  </g>

  <!-- stats and certificate mark -->
  <text class="stat-figure" x="303" y="1158" text-anchor="middle">30</text>
  <text class="stat-unit" x="303" y="1174" text-anchor="middle">SERVINGS</text>
  <circle cx="468" cy="1152" r="40" fill="none" stroke="var(--green)" stroke-width="1.5" aria-label="Certification badge"/>
  <text class="stat-figure" x="633" y="1158" text-anchor="middle">116</text>
  <text class="stat-unit" x="633" y="1174" text-anchor="middle">CALORIES</text>
</svg>
</body>
</html>
```